Business card design for holistic health care clinic

We need a double-sided business card design for our holistic health care clinic that integrates our logo design and also its color scheme. My business is called Valmira. It is an integrative medicine clinic. You have already done the logo for me. Please ensure an elegant and upscale design that is not cluttered, but still has all the necessary information (please see below for details).

Target Market(s)

Wellness, fitness, rehabilitation for educated, well-traveled open-minded clients who are focused on natural, organic, balanced and preventive healthcare and lifestyle.

Industry/Entity Type

Medical

Contact Information for Business Card

Modern, clean.

Number of Pages Required

1 page

Font styles to use
Serif
Sans Serif

Colors

Designer to choose colors to be used in the design.

Requirements
Must have
• Logo on one side, all other information on the other side.
• Other information should include:
• Tobias Wrenfeld - DOE, CPT, LMT
• 4100 East Marrow Drive
• Austin, TX 78119
• 512 555 0148
• 818 555 0192
• info@ValmiraHealth.example
• t.wrenfeld@ValmiraHealth.example
Nice to have
• Darker background on front - but not totally black - shaded/dark gray.

```html
<!DOCTYPE html>
<html lang="en">
<head>
<meta charset="utf-8">
<title>Valmira Business Card</title>
<link rel="stylesheet" href="https://fonts.googleapis.com/css2?family=Nunito:wght@700;800&family=Roboto:wght@400;500&family=Roboto+Condensed:wght@700&display=swap">
<style>
  :root {
    --page-bg: #ecebe8;
    --brand-blue: #0a90cf;
    --card-dark: #2a2a2a;
    --card-dark-edge: #202020;
    --ink-dark: #262626;
    --white: #ffffff;
  }
  * { box-sizing: border-box; margin: 0; padding: 0; }
  html, body {
    width: 1200px; height: 960px; overflow: hidden;
    background: var(--page-bg);
  }
  .canvas { position: relative; width: 1200px; height: 960px; }

  .card {
    position: absolute;
    width: 600px; height: 343px;
    overflow: hidden;
  }
  .card--front { left: 314px; top: 113px; background: radial-gradient(ellipse at 70% 30%, #333 0%, var(--card-dark) 55%, var(--card-dark-edge) 100%); }
  .card--back { left: 312px; top: 472px; background: var(--brand-blue); }

  .front-shapes { position: absolute; inset: 0; }

  .contact {
    position: absolute; left: 41px; top: 110px;
    color: var(--white);
    font-family: "Roboto", sans-serif; font-size: 14.5px; line-height: 19px;
  }
  .contact__name {
    font-family: "Roboto Condensed", sans-serif; font-weight: 700;
    font-size: 21px; line-height: 22px; letter-spacing: 0.2px;
  }
  .contact__credentials {
    font-family: "Roboto Condensed", sans-serif; font-weight: 700;
    font-size: 11px; line-height: 14px; margin-bottom: 22px;
  }
  .contact__label { font-weight: 500; }
  .contact__rule {
    border: 0; border-top: 1.5px dotted rgba(255,255,255,0.85);
    margin: 8px 0 10px;
  }
  .contact__rule--short { width: 132px; }
  .contact__rule--long { width: 168px; }

  .brand {
    position: absolute; text-align: center;
    font-family: "Nunito", sans-serif;
  }
  .brand__name { font-weight: 800; letter-spacing: 1px; }
  .brand__tagline { font-weight: 700; }

  .brand--front { left: 300px; top: 82px; width: 268px; color: var(--brand-blue); }
  .brand--front .brand__name { font-size: 54px; line-height: 58px; }
  .brand--front .brand__tagline { font-size: 14.5px; line-height: 18px; }

  .brand--back { left: 140px; top: 140px; width: 320px; color: var(--ink-dark); }
  .brand--back .brand__name { font-size: 68px; line-height: 72px; }
  .brand--back .brand__tagline { font-size: 17.5px; line-height: 20px; }

  .slogan {
    position: absolute; left: 0; right: 0; top: 291px; text-align: center;
    font-family: "Roboto", sans-serif; font-size: 14px; color: var(--ink-dark);
  }
</style>
</head>
<body>
<main class="canvas">
  <section class="card card--front" aria-label="Card front">
    <svg class="front-shapes" width="600" height="343" viewBox="0 0 600 343" aria-hidden="true">
      <polygon points="0,0 138,0 360,343 0,343" fill="var(--brand-blue)"/>
      <line x1="160" y1="14" x2="372" y2="343" stroke="var(--white)" stroke-width="4"/>
    </svg>
    <div class="contact">
      <p class="contact__name">TOBIAS WRENFELD</p>
      <p class="contact__credentials">DOE, CPT, LMT</p>
      <p><span class="contact__label">P:</span> 512 555 0148</p>
      <p><span class="contact__label">C:</span> 818 555 0192</p>
      <hr class="contact__rule contact__rule--short">
      <p>4100 East Marrow Drive</p>
      <p>Austin, TX 78119</p>
      <hr class="contact__rule contact__rule--long">
      <p>t.wrenfeld@ValmiraHealth.example</p>
      <p>www.ValmiraHealth.example</p>
    </div>
    <div class="brand brand--front">
      <p class="brand__name">VALMIRA</p>
      <p class="brand__tagline">Integrative Holistic Medicine</p>
    </div>
  </section>

  <section class="card card--back" aria-label="Card back">
    <div class="brand brand--back">
      <p class="brand__name">VALMIRA</p>
      <p class="brand__tagline">Integrative Holistic Medicine</p>
    </div>
    <p class="slogan">it’s all about you – your health, your objectives</p>
  </section>
</main>
</body>
</html>
```